Yacht, Boats, Watersports company needs a redesign of business card

Hello Designers!
We are a Boat dealership company that sells fun in the water, we sell boats, Yachts, Kayaks and also yacht WaterSport toys. We are looking to redesign our business cards in to something a little bit more sophisticated. in a way that we can make better use of our company colors. I'm attaching a zipped file containing the company 3 sets of company logo which one is an horizontal another one is a vertical and also a chromed 3d logo. Also is included two set of business cards that we use and also some designs that i think it's interesting. We use PMS 2026c Orange and PMS 7687C Blue. I would like to see at least two different options with the orange as accent and also using blue as an accent color. It's really important for the business cards to have a font option and size that is legible to most people. Our current website is wwww.coralpennant.com. Please visit if you want to have a better feeling of the Boat dealership
You can send Single sided or double side options. We are now using single sided but we may be open for a double side option if we really like the design.
Target Market(s)
Marine, boat sales, yacht sales, water toys sales/
Contact Information for Business Card
Name: Dale Whitcombe
Address: 212 North Fenwick Lane,
Harbor Point, FL 33019
Phone: 954-731-8842
Fax: 954:731-8843
Cell: 954-382-1490
Email: dw@coralpennant.com
Website: coralpennant.com
Requirements
Must have
- the current information of the business card provided.
logo
use the PMS Colors
Nice to have
- a touch of elegance and sophistication but simple
Should not have
- should not have any typography that is hard to read, the card should be simple but yet sophisticated.

```html
<!DOCTYPE html>
<html lang="en">
<head>
<meta charset="utf-8">
<title>Coral Pennant — Business Card</title>
<link rel="stylesheet" href="https://fonts.googleapis.com/css2?family=Montserrat:wght@600;700;800&family=Questrial&display=swap">
<style>
  :root {
    --brand-blue: #1c3f7e;
    --brand-orange: #e8572a;
    --card-white: #ffffff;
    --stage-dark: #2b2c2e;
    --stage-light: #4a4b4e;
    --soft-blue: rgba(255,255,255,0.06);
    --pale-circle: #eef1f7;
  }
  * { box-sizing: border-box; margin: 0; padding: 0; }
  html, body { width: 1200px; height: 1000px; overflow: hidden; }
  body {
    background: radial-gradient(ellipse at 60% 35%, var(--stage-light), var(--stage-dark) 75%);
    font-family: "Montserrat", Arial, sans-serif;
    position: relative;
  }
  .card {
    position: absolute;
    width: 580px;
    height: 330px;
    border-radius: 26px;
    overflow: hidden;
    box-shadow: 0 18px 40px rgba(0,0,0,0.45);
  }

  /* Front side */
  .card-front {
    left: 70px; top: 110px;
    background: var(--brand-blue);
  }
  .card-front .faint-circle {
    position: absolute;
    right: -60px; top: -90px;
    width: 340px; height: 340px;
    border-radius: 50%;
    background: var(--soft-blue);
  }
  .front-brand {
    position: absolute;
    left: 48px; top: 150px;
    display: flex; align-items: center; gap: 18px;
  }
  .front-brand .brand-dot {
    width: 64px; height: 64px; border-radius: 50%;
    background: var(--brand-orange);
  }
  .front-brand .brand-name {
    color: var(--card-white);
    font-weight: 800;
    font-size: 40px;
    letter-spacing: 2px;
    line-height: 1.05;
    text-transform: uppercase;
  }

  /* Back side */
  .card-back {
    left: 550px; top: 540px;
    background: var(--card-white);
  }
  .back-circle {
    position: absolute;
    left: -110px; top: 20px;
    width: 400px; height: 400px;
    border-radius: 50%;
    background: var(--pale-circle);
  }
  .holder {
    position: absolute;
    left: 40px; top: 222px;
    font-weight: 700;
    font-size: 22px;
    line-height: 1.1;
  }
  .holder .holder-name { color: var(--brand-blue); }
  .holder .holder-role { color: var(--brand-orange); }

  .back-brand {
    position: absolute;
    right: 30px; top: 28px;
    display: flex; align-items: center; gap: 8px;
  }
  .back-brand .brand-dot {
    width: 22px; height: 22px; border-radius: 50%;
    background: var(--brand-orange);
  }
  .back-brand .brand-name {
    color: var(--brand-blue);
    font-weight: 800;
    font-size: 14px;
    letter-spacing: 1px;
    text-transform: uppercase;
  }

  .address {
    position: absolute;
    right: 30px; top: 72px;
    text-align: right;
    color: var(--brand-blue);
    font-weight: 700;
    font-style: normal;
    font-size: 15px;
    line-height: 1.3;
    letter-spacing: 0.5px;
  }
  .contact-list {
    position: absolute;
    right: 30px; top: 128px;
    list-style: none;
    text-align: right;
  }
  .contact-list li {
    display: flex; justify-content: flex-end; align-items: center; gap: 8px;
    font-family: "Questrial", Arial, sans-serif;
    color: var(--brand-blue);
    font-size: 14px;
    letter-spacing: 1px;
    height: 22px;
  }
  .contact-list svg { width: 16px; height: 16px; }

  .online {
    position: absolute;
    right: 30px; top: 252px;
    text-align: right;
    font-family: "Questrial", Arial, sans-serif;
    font-size: 15px;
    letter-spacing: 1px;
    line-height: 1.5;
    color: var(--brand-blue);
  }
  .online .accent { color: var(--brand-orange); }
</style>
</head>
<body>

<section class="card card-front" aria-label="Card front">
  <div class="faint-circle"></div>
  <div class="front-brand">
    <span class="brand-dot"></span>
    <span class="brand-name">Coral<br>Pennant</span>
  </div>
</section>

<section class="card card-back" aria-label="Card back">
  <div class="back-circle"></div>
  <div class="holder">
    <div class="holder-name">DALE WHITCOMBE</div>
    <div class="holder-role">CEO</div>
  </div>

  <div class="back-brand">
    <span class="brand-dot"></span>
    <span class="brand-name">Coral Pennant</span>
  </div>

  <address class="address">
    212 North Fenwick Lane,<br>Harbor Point, FL 33019
  </address>

  <ul class="contact-list">
    <li>954-731-8842
      <svg viewBox="0 0 16 16" aria-label="Phone"><circle cx="8" cy="8" r="8" fill="#e8572a"/><path d="M5 4.5c.5-.5 1-.4 1.3.1l.6 1c.2.4.1.8-.2 1l-.4.3c.4.9 1.1 1.6 2 2l.3-.4c.3-.3.7-.4 1-.2l1 .6c.5.3.6.8.1 1.3-.6.7-1.5.8-2.4.3C6.9 9.6 6.4 9.1 5.5 7.9 4.7 6.7 4.5 5.2 5 4.5z" fill="#fff"/></svg>
    </li>
    <li>954-382-1490
      <svg viewBox="0 0 16 16" aria-label="Cell"><circle cx="8" cy="8" r="8" fill="#e8572a"/><rect x="5.5" y="3.5" width="5" height="9" rx="1" fill="none" stroke="#fff" stroke-width="1.2"/></svg>
    </li>
    <li>954:731-8843
      <svg viewBox="0 0 16 16" aria-label="Fax"><circle cx="8" cy="8" r="8" fill="#e8572a"/><rect x="4" y="6.5" width="8" height="4.5" rx="0.8" fill="#fff"/><rect x="5.5" y="4" width="5" height="2.5" fill="#fff"/></svg>
    </li>
    <li>954:731-8843.com
      <svg viewBox="0 0 16 16" aria-label="Email"><circle cx="8" cy="8" r="8" fill="#e8572a"/><rect x="4" y="5" width="8" height="6" rx="0.6" fill="#fff"/><path d="M4.3 5.3 8 8.3l3.7-3" fill="none" stroke="#e8572a" stroke-width="0.9"/></svg>
    </li>
    <li>coralpennant.com
      <svg viewBox="0 0 16 16" aria-label="Website"><circle cx="8" cy="8" r="8" fill="#e8572a"/><circle cx="8" cy="8" r="4" fill="none" stroke="#fff" stroke-width="1"/><path d="M4 8h8M8 4c-1.6 2.2-1.6 5.8 0 8M8 4c1.6 2.2 1.6 5.8 0 8" fill="none" stroke="#fff" stroke-width="0.8"/></svg>
    </li>
  </ul>

  <div class="online">
    <div>dw@<span class="accent">coralpennant</span>.com</div>
    <div>www.<span class="accent">coralpennant</span>.com</div>
  </div>
</section>

</body>
</html>
```